Harborline Lending and Capital. We provide MOSTLY residential home mortgages in Florida AND commercial loans for investment properties throughout the United states.
I would love to emulate so of the lender sites that are available on the internet but I would like to have the site as popular as possible for SEO purposes. Clients can already click the link to take them to the mortgage application where they can complete that and upload documents. If you could polish that up for me that would be great. I can also provide you with great detail on loan programs that are currently being offered. WE OFFER ALL MORTGAGE LENDING PRODUCTS. I would also like to add something in reference to the rate but I don't think it's legal to actually state or promise a rate for mortgage since they vary based on loan type, client and other criteria...

On the Harborline real estate site I would like to add a link or some way for clients to be able to put in credit card information to render services ...

Please let me know what you need from me

Thank you !!

Current link to site to improve and code

https://harborlinelendingandcapital.example/

Industry/Entity Type

Residential and commmercial lending

Coding

Coded - Design and coding required

Number of Pages Required

2 page

Requirements
Must have
• Love to integrate Mortgage interest rates even if general
Nice to have
• Link to fill out mortgage application via Quorvel LPX software

```html
<!DOCTYPE html>
<html lang="en">
<head>
<meta charset="utf-8">
<title>Harborline Lending and Capital</title>
<link href="https://fonts.googleapis.com/css2?family=Poppins:wght@300;400;500;600;700&display=swap" rel="stylesheet">
<style>
:root{
  --green-dark:#1d3a14;
  --green-deep:#14290d;
  --green-accent:#8cb32b;
  --green-soft:#f3f8ec;
  --ink:#1b1b1b;
  --text:#3c3c3c;
  --white:#ffffff;
  --footer:#1c1c1c;
  --footer-panel:#262626;
  --field:#2f2f2f;
}
*{box-sizing:border-box;margin:0;padding:0}
html,body{width:1200px;height:4988px;overflow:hidden}
body{font-family:"Poppins",sans-serif;color:var(--text);background:var(--white);position:relative}
.accent{color:var(--green-accent)}
section,header,footer{position:relative;width:1200px}
.abs{position:absolute}

/* header */
.site-header{height:112px;background:var(--white)}
.brand{left:112px;top:16px;display:flex;align-items:center;gap:14px}
.brand-mark{width:64px;height:64px;border-radius:50%;background:var(--green-dark)}
.brand-name{font-size:13px;font-weight:600;color:var(--green-dark);text-transform:uppercase;letter-spacing:1px;line-height:1.5;width:260px}
.contact-bar{right:112px;top:20px;display:flex;gap:36px;font-size:12px;color:var(--ink)}
.contact-item{display:flex;align-items:center;gap:12px}
.contact-icon{width:30px;height:30px;border-radius:50%;background:#e6f0d6;display:flex;align-items:center;justify-content:center}
.main-nav{right:112px;top:74px;display:flex;gap:40px;font-size:12.5px;color:var(--ink);text-transform:uppercase}
.main-nav a{color:inherit;text-decoration:none}

/* hero */
.hero{height:474px;background:linear-gradient(90deg,#14290d 0%,#1f3a17 45%,#2f4e26 70%,#6b7a5e 100%);overflow:hidden}
.hero-photo{right:0;top:0;width:620px;height:474px;background:linear-gradient(90deg,rgba(29,58,20,0) 0%,#6f7d5e 40%,#8d8576 70%,#5b5a50 100%)}
.hero-copy{left:85px;top:78px;width:560px;color:var(--white)}
.hero-title{font-size:25px;font-weight:600;line-height:1.78;text-transform:uppercase}
.hero-text{font-size:14.5px;line-height:2.35;margin-top:22px}
.btn-outline{display:inline-block;border:1.5px solid var(--green-accent);border-radius:40px;color:var(--green-accent);text-transform:uppercase;font-size:14px;padding:9px 22px;text-decoration:none;background:transparent;white-space:nowrap}
.hero .btn-outline{margin-top:30px;font-size:13px}

/* section headings */
.section-title{text-align:center;font-size:31px;font-weight:600;color:var(--ink);text-transform:uppercase;letter-spacing:-.5px}
.divider{display:flex;align-items:center;justify-content:center;gap:10px;margin-top:12px}
.divider span{width:44px;height:2px;background:var(--ink)}
.divider i{width:20px;height:20px;border-radius:50%;background:var(--green-dark);display:block}

/* programs */
.programs{height:798px;background:var(--green-soft)}
.programs .section-head{position:absolute;top:76px;width:100%}
.slider-arrow{width:38px;height:38px;border:2px solid var(--ink);border-radius:50%;display:flex;align-items:center;justify-content:center}
.program-card{top:204px;width:316px;height:516px;background:var(--white);border-radius:10px;text-align:center;padding:12px}
.program-card.featured{background:var(--green-dark);color:var(--white)}
.program-photo{height:228px;border-radius:8px}
.program-name{font-size:16px;font-weight:400;color:var(--green-accent);text-transform:uppercase;margin-top:30px}
.program-text{font-size:14px;line-height:2.45;margin:12px 14px 0}
.btn-solid{display:inline-block;background:var(--green-accent);color:var(--white);border-radius:40px;font-size:13.5px;text-transform:uppercase;padding:10px 22px;text-decoration:none}
.program-card .btn-solid{margin-top:18px}

/* about */
.about{height:661px;background:var(--white)}
.about-emblem{left:110px;top:86px;width:403px;height:494px;display:flex;flex-direction:column;align-items:center;justify-content:center;gap:28px}
.about-emblem .circle{width:300px;height:300px;border-radius:50%;background:var(--green-dark)}
.about-emblem .name{font-size:22px;font-weight:600;color:var(--green-dark);text-transform:uppercase;text-align:center}
.about-copy{left:598px;top:80px;width:500px}
.about-title{font-size:31px;font-weight:600;color:var(--ink);text-transform:uppercase;line-height:1.65}
.about-title .divider{display:inline-flex;margin:0 0 0 16px;vertical-align:middle}
.about-text{font-size:14.5px;line-height:2.55;margin-top:20px;color:var(--ink)}
.about .btn-outline{margin-top:22px;font-size:13px;padding:8px 20px}

/* products */
.products{height:1783px;background:var(--green-soft)}
.products .section-head{position:absolute;top:66px;width:100%}
.product-copy{width:480px}
.product-name{font-size:24px;font-weight:400;color:var(--ink);text-transform:uppercase}
.product-name.accent-name{color:var(--green-accent)}
.product-text{font-size:14px;line-height:2.4;margin-top:14px;color:var(--ink)}
.product-sub{display:flex;align-items:center;gap:14px;font-size:19px;color:var(--ink);text-transform:uppercase;margin:26px 0 0 24px}
.product-sub b{width:22px;height:22px;background:var(--green-accent);border-radius:3px;display:block}
.product-detail{font-size:13.5px;margin:18px 0 0 24px;color:var(--ink)}
.rate-pill{display:inline-block;margin-top:36px;background:var(--green-dark);color:var(--white);font-size:14px;font-weight:500;text-transform:uppercase;padding:10px 20px;border-radius:40px}
.rate-pill.light{background:var(--green-accent)}
.product-photo{width:452px;height:416px;border-radius:14px;border:2px solid var(--ink)}
.product-photo.framed-accent{border-color:var(--green-accent)}
.products .btn-outline{left:478px;top:1680px;width:244px;text-align:center}

/* properties */
.properties{height:706px;background:var(--white)}
.properties .section-head{position:absolute;top:80px;width:100%}
.property-card{top:206px;width:230px;height:327px;border-radius:8px;display:flex;align-items:flex-end;justify-content:center;padding-bottom:26px;color:var(--white);font-size:17px;font-weight:600;text-transform:uppercase}
.properties .btn-outline{left:496px;top:584px;width:208px;text-align:center}

/* footer */
.site-footer{height:454px;background:var(--footer);color:var(--white)}
.footer-brand{left:88px;top:70px;display:flex;align-items:center;gap:18px}
.footer-brand .brand-mark{width:100px;height:100px;background:var(--white)}
.footer-brand .brand-name{color:var(--white);font-size:11px;width:290px}
.footer-nav{left:88px;top:232px;display:flex;gap:12px;font-size:12px;text-transform:uppercase}
.footer-nav a{color:var(--white);text-decoration:none}
.copyright{left:88px;top:282px;font-size:11px;text-transform:uppercase}
.socials{left:88px;top:334px;display:flex;gap:8px}
.socials span{width:32px;height:32px;border:1.5px solid var(--white);border-radius:50%}
.contact-panel{left:623px;top:46px;width:488px;height:408px;background:var(--footer-panel);border-radius:16px 16px 0 0}
.contact-title{text-align:center;font-size:30px;font-weight:500;text-transform:uppercase;margin-top:28px}
.field{margin:0 20px;background:var(--field);border-radius:6px;height:40px;font-size:12px;color:#9a9a9a;text-transform:uppercase;padding:12px 20px}
.field.message{height:88px}
.contact-panel .btn-solid{position:absolute;left:166px;bottom:30px;width:156px;text-align:center}
</style>
</head>
<body>

<header class="site-header">
  <div class="brand abs">
    <div class="brand-mark"></div>
    <div class="brand-name">Harborline Lending and Capital</div>
  </div>
  <div class="contact-bar abs">
    <div class="contact-item">
      <span class="contact-icon"><svg width="14" height="14" viewBox="0 0 24 24"><path d="M6.6 10.8a15 15 0 0 0 6.6 6.6l2.2-2.2c.3-.3.7-.4 1-.2 1.1.4 2.3.6 3.6.6.6 0 1 .4 1 1V20c0 .6-.4 1-1 1A17 17 0 0 1 3 4c0-.6.4-1 1-1h3.5c.6 0 1 .4 1 1 0 1.3.2 2.5.6 3.6.1.3 0 .7-.2 1z" fill="#8cb32b"/></svg></span>
      +1 555 010 0199
    </div>
    <div class="contact-item">
      <span class="contact-icon"><svg width="14" height="14" viewBox="0 0 24 24"><path d="M3 5h18v14H3z" fill="#8cb32b"/><path d="M3 5l9 7 9-7" stroke="#fff" stroke-width="1.6" fill="none"/></svg></span>
      HELLO@HARBORLINE.EXAMPLE
    </div>
  </div>
  <nav class="main-nav abs">
    <a href="#">Home</a><a href="#">About Us</a><a href="#">Properties</a><a href="#">Mortgage</a><a href="#">Contact Us</a>
  </nav>
</header>

<section class="hero">
  <div class="hero-photo abs" role="img" aria-label="Three people reviewing a loan on a tablet"></div>
  <div class="hero-copy abs">
    <h1 class="hero-title">Your trusted partner in <span class="accent">residential<br>&amp; commercial mortgages</span> in<br>Florida &amp; nationwide.</h1>
    <p class="hero-text">Residential home loans in florida and commercial lending in america Your best resource for hassle-free, low cost mortgage origination</p>
    <a class="btn-outline" href="#">Fill out mortgage application to begin lending process</a>
  </div>
</section>

<section class="programs">
  <div class="section-head">
    <h2 class="section-title">Our Loan <span class="accent">Programs</span></h2>
    <div class="divider"><span></span><i></i><span></span></div>
  </div>
  <div class="slider-arrow abs" style="left:33px;top:442px"><svg width="18" height="18" viewBox="0 0 24 24"><path d="M20 12H5M11 5l-7 7 7 7" stroke="#1b1b1b" stroke-width="2.4" fill="none"/></svg></div>
  <div class="slider-arrow abs" style="left:1118px;top:442px"><svg width="18" height="18" viewBox="0 0 24 24"><path d="M4 12h15M13 5l7 7-7 7" stroke="#1b1b1b" stroke-width="2.4" fill="none"/></svg></div>

  <article class="program-card abs" style="left:110px">
    <div class="program-photo" role="img" aria-label="Conventional mortgage folder with keys on a desk" style="background:linear-gradient(135deg,#8a5a3a,#e9e3da 50%,#5b3f2c)"></div>
    <h3 class="program-name">Conventional Loans</h3>
    <p class="program-text">Typically require a 3% down payment for first-time homebuyers, or 5%–20% for other buyers.</p>
    <a class="btn-solid" href="#">Learn More</a>
  </article>
  <article class="program-card featured abs" style="left:442px">
    <div class="program-photo" role="img" aria-label="Wooden house model labelled FHA loan" style="background:linear-gradient(135deg,#6d4a30,#d9b98f 55%,#7a5637)"></div>
    <h3 class="program-name">FHA Loans</h3>
    <p class="program-text">Credit scores of 580+ (for 3.5% down payment), or 500–579 with a 10% down payment.</p>
    <a class="btn-solid" href="#">Learn More</a>
  </article>
  <article class="program-card abs" style="left:774px">
    <div class="program-photo" role="img" aria-label="USDA home loan agreement on a clipboard" style="background:linear-gradient(135deg,#a56a3f,#eceae6 50%,#b2202c)"></div>
    <h3 class="program-name">USDA Loans</h3>
    <p class="program-text">Must meet the USDA's income limits and purchase a home in a designated rural area.</p>
    <a class="btn-solid" href="#">Learn More</a>
  </article>
</section>

<section class="about">
  <div class="about-emblem abs">
    <div class="circle"></div>
    <div class="name">Harborline Lending and Capital</div>
  </div>
  <div class="about-copy abs">
    <h2 class="about-title">About Harborline <span class="accent">Mortgage<br>and Finance</span><span class="divider"><span></span><i></i><span></span></span></h2>
    <p class="about-text">Harborline Mortgage Originates Residential Home loans in Florida and Commercial and business financing in all 50 States. We have over 25 years of experience in ALL types of real estate and commercial lending. We are strategically partnered to help you obtain ALL necessary components of residential and commercial lending. From the RIGHT lending partners to the best practice Insurance avenues and commercial and residential real estate partners</p>
    <a class="btn-outline" href="#">Contact Us</a>
  </div>
</section>

<section class="products">
  <div class="section-head">
    <h2 class="section-title">Mortgage Lending <span class="accent">Products</span></h2>
    <div class="divider"><span></span><i></i><span></span></div>
  </div>

  <div class="product-copy abs" style="left:110px;top:200px">
    <h3 class="product-name">Conventional Loans</h3>
    <p class="product-text">Conventional loans are not backed by the government and are typically used for primary residences, second homes, and investment properties.</p>
    <div class="product-sub"><b></b>Eligibility</div>
    <p class="product-detail">Credit score of 620 or higher, down payment of 3% to 20%.</p>
    <div class="product-sub"><b></b>Typical Terms</div>
    <p class="product-detail">15, 20, or 30 years.</p>
    <span class="rate-pill">Fixed-Rate: 6.00% - 7.50%</span>
  </div>
  <div class="product-photo abs" style="left:633px;top:205px;background:linear-gradient(135deg,#d8dde3,#f3e7a8 50%,#4a78b8)" role="img" aria-label="Spiral notepad reading conventional loan with charts and pens"></div>

  <div class="product-photo framed-accent abs" style="left:110px;top:712px;background:linear-gradient(135deg,#3b3b3b,#e7eaee 45%,#c9d3df)" role="img" aria-label="FHA loan application form with calculator and pen"></div>
  <div class="product-copy abs" style="left:625px;top:705px">
    <h3 class="product-name accent-name">FHA Loans</h3>
    <p class="product-text">FHA loans are backed by the government and ideal for first-time homebuyers or those with less-than-perfect credit. They allow lower down payments and easier qualification.</p>
    <div class="product-sub"><b></b>Eligibility</div>
    <p class="product-detail">Credit score of 580 for a 3.5% down payment, or 500 for a 10%</p>
    <div class="product-sub"><b></b>Typical Terms</div>
    <p class="product-detail">15, 20, 30 years.</p>
    <span class="rate-pill light">Fixed-Rate: 6.25% - 7.75%</span>
  </div>

  <div class="product-copy abs" style="left:110px;top:1197px">
    <h3 class="product-name">USDA Loans</h3>
    <p class="product-text">USDA loans are designed for rural and suburban homebuyers who meet specific income and location requirements, offering no down payment.</p>
    <div class="product-sub"><b></b>Eligibility</div>
    <p class="product-detail">Income limits apply based on family size and geographic area.</p>
    <div class="product-sub"><b></b>Typical Terms</div>
    <p class="product-detail">30 years.</p>
    <span class="rate-pill">Fixed-Rate: 6.25% - 7.00%</span>
  </div>
  <div class="product-photo abs" style="left:633px;top:1205px;background:linear-gradient(135deg,#5d6f82,#c9b27a 50%,#8c9aa8)" role="img" aria-label="House keychain tagged USDA loan resting on banknotes"></div>

  <a class="btn-outline abs" href="#">View More Products</a>
</section>

<section class="properties">
  <div class="section-head">
    <h2 class="section-title">Available <span class="accent">Properties</span></h2>
    <div class="divider"><span></span><i></i><span></span></div>
  </div>
  <div class="property-card abs" style="left:112px;background:linear-gradient(180deg,#e9ecef,#8a8f94 60%,#2a2a2a)" role="img" aria-label="Modern white house with dark windows">12 Sunset Street</div>
  <div class="property-card abs" style="left:361px;background:linear-gradient(180deg,#cfd8de,#23313f 55%,#1b1b1b)" role="img" aria-label="Dark modern house among trees">34 Union Avenue</div>
  <div class="property-card abs" style="left:610px;background:linear-gradient(180deg,#8aa3c7,#6c7683 55%,#2b2b2b)" role="img" aria-label="Contemporary building with patterned facade">56 Washington Street</div>
  <div class="property-card abs" style="left:859px;background:linear-gradient(180deg,#bcc7cf,#7a3a2c 50%,#2a2a2a)" role="img" aria-label="Brick and glass modern building">78 Oak Boulevard</div>
  <a class="btn-outline abs" href="#">View Properties</a>
</section>

<footer class="site-footer">
  <div class="footer-brand abs">
    <div class="brand-mark"></div>
    <div class="brand-name">Harborline Lending and Capital</div>
  </div>
  <nav class="footer-nav abs">
    <a href="#">Home</a><span>|</span><a href="#">About Us</a><span>|</span><a href="#">Properties</a><span>|</span><a href="#">Mortgage</a><span>|</span><a href="#">Contact Us</a>
  </nav>
  <p class="copyright abs">© 2025. All rights reserved.</p>
  <div class="socials abs"><span></span><span></span><span></span></div>

  <form class="contact-panel abs">
    <h2 class="contact-title">Get in <span class="accent">Touch</span></h2>
    <div class="field" style="margin-top:26px">Full Name</div>
    <div class="field" style="margin-top:20px">Email Address or Phone Number</div>
    <div class="field message" style="margin-top:20px">Type your message</div>
    <a class="btn-solid" href="#">Send Message</a>
  </form>
</footer>

</body>
</html>
```